Brenlow Estates Website and Logo Design

We need a new logo and website designed for 'Brenlow Estates Ltd', which is a well established Guernsey property holding company founded in 1934.

The company does not currently have a website. The new website should be similar in style and layout to https://www.quorvanhall.example/.

Target Market(s)

Industry, Media, Tenants

Industry/Entity Type

Property Management

Logo Text

BEL OR Brenlow Estates Ltd OR BE

Coding

Coded - Design and coding required

Number of Pages Required

4 page

Font styles to use
Other font styles liked:
• Helvetica

Requirements
Must have
• The logo laying over the picture (like https://www.quorvanhall.example/).
• Big pictures on homepage (like https://www.quorvanhall.example/)

```html
<!DOCTYPE html>
<html lang="en">
<head>
<meta charset="utf-8">
<title>Brenlow Estates</title>
<link rel="stylesheet" href="https://fonts.googleapis.com/css2?family=Roboto:wght@300;400;500;700&display=swap">
<style>
:root{
  --red:#e3241b;
  --ink:#222;
  --text:#555;
  --muted:#999;
  --line:#ddd;
  --soft:#f5f5f5;
  --footer:#2b2b2b;
  --footer-base:#1f1f1f;
  --white:#fff;
}
*{box-sizing:border-box;margin:0;padding:0}
html,body{width:1200px;height:2575px;overflow:hidden}
body{font-family:"Roboto",Helvetica,Arial,sans-serif;color:var(--text);background:var(--white);position:relative}
.abs{position:absolute}
/* hero */
.hero{position:absolute;left:0;top:0;width:1200px;height:590px;background:linear-gradient(180deg,#9fb0c4 0%,#c9d3dd 38%,#e8e6e0 55%,#8a8478 72%,#5b6a3f 88%,#3f4a33 100%)}
.brand{position:absolute;left:90px;top:28px;display:flex;align-items:center;gap:10px}
.brand-mark{width:34px;height:34px;background:var(--red)}
.brand-name{font-weight:700;font-size:20px;color:var(--ink);line-height:1}
.brand-name small{display:block;font-size:9px;letter-spacing:1px;margin-top:3px}
.nav{position:absolute;top:38px;right:88px;display:flex;gap:20px;font-size:13px;color:var(--ink)}
.nav a{color:inherit;text-decoration:none;padding-bottom:4px}
.nav a.active{color:var(--red);border-bottom:2px solid var(--red)}
.hero-copy{position:absolute;left:0;top:180px;width:1200px;text-align:center;color:var(--ink)}
.hero-copy h3{font-weight:400;font-size:20px}
.hero-copy h1{font-weight:700;font-size:46px;margin-top:4px}
.hero-copy p{font-size:13px;line-height:21px;width:420px;margin:10px auto 0}
.btn-red{display:inline-block;margin-top:14px;background:var(--red);color:var(--white);font-size:12px;border-radius:18px;width:120px;height:34px;line-height:34px}
.arrow{position:absolute;top:313px;width:38px;height:38px;border-radius:50%;display:flex;align-items:center;justify-content:center}
.arrow.prev{left:26px;background:#333}
.arrow.next{right:26px;background:var(--red)}
/* section heads */
.section-title{position:absolute;left:0;width:1200px;text-align:center;font-weight:400;font-size:27px;color:var(--ink)}
.divider{position:absolute;left:500px;width:200px;height:14px}
/* about */
.about-text{position:absolute;left:160px;top:696px;width:880px;text-align:center;font-size:13px;line-height:20px;color:var(--muted)}
.btn-ghost{position:absolute;left:540px;top:769px;width:120px;height:38px;line-height:36px;border:1px solid #ccc;border-radius:19px;text-align:center;font-size:12px;color:var(--text)}
/* property */
.property{position:absolute;left:0;top:850px;width:1200px;height:768px;background:var(--soft)}
.filters{position:absolute;left:0;top:963px;width:1200px;display:flex;justify-content:center;gap:34px;font-size:13px;color:var(--muted)}
.filters .on{color:var(--red)}
.tile{position:absolute}
.tile-card{background:#1e1e1e;color:var(--white);padding:34px 24px}
.tile-card h4{font-size:14px;font-weight:700}
.tile-card p{font-size:11px;line-height:18px;margin-top:8px}
.tile-card .tag{display:inline-block;margin-top:14px;border:1px solid var(--white);font-size:10px;padding:8px 22px}
.tile-card .corner{position:absolute;right:0;bottom:0;width:0;height:0;border-left:54px solid transparent;border-bottom:54px solid var(--red)}
/* blog */
.post-photo{position:absolute;height:180px;clip-path:polygon(0 0,100% 0,76% 100%,0 100%)}
.post-card{position:absolute;width:334px;height:184px;background:var(--white);box-shadow:0 0 8px rgba(0,0,0,.1);padding:26px 16px 0 92px}
.post-card h4{font-weight:400;font-size:15px;color:var(--ink)}
.post-meta{font-size:11px;color:var(--text);margin-top:6px;display:flex;gap:10px}
.post-meta .heart{color:var(--red)}
.post-card hr{border:0;border-top:1px solid #999;width:24px;margin:10px 0}
.post-card p{font-size:11px;line-height:15px;color:var(--muted)}
.post-card .more{font-size:11px;color:var(--ink);margin-top:12px}
/* testimonials */
.quote{position:absolute;top:2093px;width:316px;height:156px;background:var(--white);border:1px solid #eee;padding:26px 20px 0 56px}
.quote.raised{box-shadow:0 0 12px rgba(0,0,0,.12)}
.quote h5{font-weight:400;font-size:15px;color:var(--ink)}
.quote .role{font-size:12px;color:var(--text);margin-top:4px}
.quote p{font-size:11px;line-height:17px;color:var(--muted);margin-top:6px}
.stars{color:#f5a623;font-size:14px;letter-spacing:2px;margin-top:4px}
.avatar{position:absolute;top:2142px;width:52px;height:52px;border-radius:50%;background:#9a8f84;border:3px solid var(--white)}
/* footer */
.footer{position:absolute;left:0;top:2303px;width:1200px;height:226px;background:var(--footer);color:var(--white)}
.footer h6{position:absolute;top:40px;font-weight:400;font-size:15px}
.footer-about{position:absolute;left:89px;top:100px;width:270px;font-size:11px;line-height:22px}
.links{position:absolute;left:440px;top:72px;list-style:none;font-size:11px;line-height:22px}
.links li::before{content:"› ";color:var(--red)}
.social{position:absolute;left:700px;top:70px;list-style:none;font-size:11px}
.social li{display:flex;align-items:center;gap:12px;height:40px}
.social .dot{width:28px;height:28px;border-radius:50%;border:1px solid var(--white)}
.social .dot.fill{background:#3b5998;border-color:#3b5998}
.social .blue{color:#3b5998}
.contact{position:absolute;left:989px;top:74px;list-style:none;font-size:11px;line-height:16px}
.contact li{display:flex;gap:10px;margin-bottom:10px}
.contact svg{flex:none;margin-top:2px}
.base{position:absolute;left:0;top:2529px;width:1200px;height:46px;background:var(--footer-base);color:var(--white);font-size:11px}
.base .copy{position:absolute;left:89px;top:16px}
.base .legal{position:absolute;right:90px;top:16px}
.to-top{position:absolute;left:1138px;top:2510px;width:34px;height:34px;border-radius:50%;background:var(--red);display:flex;align-items:center;justify-content:center}
</style>
</head>
<body>

<header class="hero" role="img" aria-label="Photo of a modern white single-storey villa with terrace chairs and garden under an evening sky">
  <div class="brand"><span class="brand-mark"></span><span class="brand-name">Brenlow Estates<small>LTD</small></span></div>
  <nav class="nav"><a class="active">Home</a><a>About us</a><a>Services</a><a>Property</a><a>Blog</a><a>Contact Us</a></nav>
  <div class="hero-copy">
    <h3>Welcome To</h3>
    <h1>Brenlow Estates</h1>
    <p>Lorem ipsum dolor sit amet, consectetur adipiscing elit, sed do eius-mod tempor incididunt ut labore et dolore magna aliqua.</p>
    <span class="btn-red">Read More</span>
  </div>
  <span class="arrow prev"><svg width="10" height="10" viewBox="0 0 10 10"><path d="M7 1 3 5l4 4" stroke="#fff" stroke-width="2" fill="none"/></svg></span>
  <span class="arrow next"><svg width="10" height="10" viewBox="0 0 10 10"><path d="M3 1l4 4-4 4" stroke="#fff" stroke-width="2" fill="none"/></svg></span>
</header>

<section class="about">
  <h2 class="section-title" style="top:628px">About Us</h2>
  <svg class="divider" style="top:668px" viewBox="0 0 200 14"><line x1="0" y1="7" x2="80" y2="7" stroke="#ddd"/><line x1="120" y1="7" x2="200" y2="7" stroke="#ddd"/><rect x="93" y="2" width="14" height="10" fill="#ccc"/></svg>
  <p class="about-text">Lorem ipsum dolor sit amet, consectetur adipiscing elit, sed do eiusmod tempor incididunt ut labore et dolore magna aliqua. Ut enim ad minim veniam, quis nostrud exercitation ullamco laboris nisi ut aliquip ex ea commodo consequat. Duis aute irure dolor in reprehenderit in voluptate velit esse cillum dolore eu fugiat nulla pariatur. Excepteur sint occaecat cupidatat non proident, sunt in culpa qui.</p>
  <span class="btn-ghost">Read More</span>
</section>

<section class="property"></section>
<h2 class="section-title" style="top:885px">Our Property</h2>
<svg class="divider" style="top:929px" viewBox="0 0 200 14"><line x1="0" y1="7" x2="80" y2="7" stroke="#ddd"/><line x1="120" y1="7" x2="200" y2="7" stroke="#ddd"/><rect x="93" y="2" width="14" height="10" fill="#ccc"/></svg>
<div class="filters"><span class="on">All</span><span>Flats</span><span>Painthouse</span><span>Offices</span><span>Banglo</span></div>
<div class="tile" style="left:199px;top:1001px;width:263px;height:179px;background:linear-gradient(180deg,#4a78b8,#6d7f8e 60%,#3a3f44)" role="img" aria-label="Photo of glass office towers by the waterfront"></div>
<div class="tile tile-card" style="left:199px;top:1190px;width:263px;height:179px">
  <h4>HARBOUR, QUAY STREET</h4>
  <p>Level 4, 18 Quay Street,<br>St Peter Port GY1 2AB</p>
  <span class="tag">FOR RENT</span>
  <span class="corner"></span>
</div>
<div class="tile" style="left:477px;top:1001px;width:545px;height:368px;background:linear-gradient(180deg,#5c4f86,#7a6a9a 45%,#5a4640 75%,#6e5b74)" role="img" aria-label="Photo of a lit two-storey modern house with pool at dusk"></div>
<div class="tile" style="left:199px;top:1382px;width:263px;height:179px;background:linear-gradient(180deg,#2f6fd0,#4f78a8 55%,#2c3440)" role="img" aria-label="Photo of city skyscrapers against blue sky"></div>
<div class="tile" style="left:477px;top:1382px;width:263px;height:179px;background:linear-gradient(180deg,#e8e8e8,#b8b8b8 60%,#6a6a6a)" role="img" aria-label="Photo of a modern meeting room"></div>
<div class="tile" style="left:757px;top:1382px;width:265px;height:179px;background:linear-gradient(180deg,#b9a58c,#6d5c4c 60%,#1d1b1a)" role="img" aria-label="Photo of an office desk interior"></div>

<section class="blog">
  <h2 class="section-title" style="top:1656px">Blog</h2>
  <svg class="divider" style="top:1702px" viewBox="0 0 200 14"><line x1="0" y1="7" x2="80" y2="7" stroke="#ddd"/><line x1="120" y1="7" x2="200" y2="7" stroke="#ddd"/><rect x="93" y="2" width="14" height="10" fill="#ccc"/></svg>
  <article>
    <div class="post-card" style="left:245px;top:1763px;padding-left:92px">
      <h4>This is a standard post</h4>
      <div class="post-meta"><span>▢ 214 Comments</span><span><span class="heart">♥</span> 895</span></div>
      <hr>
      <p>Lorem ipsum dolor amet, consectetur adipisicing elit Impedit dolorem ipsum dolor amet, consectetur.</p>
      <div class="more">Read More →</div>
    </div>
    <div class="post-photo" style="left:89px;top:1745px;width:256px;background:linear-gradient(180deg,#3d8fe0,#9cc4e6 50%,#8a6a3c 80%,#6b5a2a)" role="img" aria-label="Photo of a brick house among palm trees"></div>
  </article>
  <article>
    <div class="post-card" style="left:776px;top:1763px">
      <h4>This is a standard post</h4>
      <div class="post-meta"><span>▢ 220 Comments</span><span><span class="heart">♥</span> 600</span></div>
      <hr>
      <p>Lorem ipsum dolor amet, consectetur adipisicing elit Impedit dolorem ipsum dolor amet, consectetur.</p>
      <div class="more">Read More →</div>
    </div>
    <div class="post-photo" style="left:620px;top:1745px;width:256px;background:linear-gradient(180deg,#c9b9a8,#8a6e5c 55%,#3a2a22)" role="img" aria-label="Photo of a dining room with chandelier"></div>
  </article>
</section>

<section class="testimonials">
  <h2 class="section-title" style="top:1993px">Client Testimonials</h2>
  <svg class="divider" style="top:2039px;left:493px" viewBox="0 0 200 14"><line x1="0" y1="7" x2="80" y2="7" stroke="#ddd"/><line x1="120" y1="7" x2="200" y2="7" stroke="#ddd"/><rect x="93" y="2" width="14" height="10" fill="#ccc"/></svg>
  <div class="quote" style="left:106px"><h5>Marek Tolland</h5><div class="role">Service: Geotechnical Conculting</div><p>Vivamus elementum semper nisi aenean eleifend tellus aenean leo ligula, porttitor.</p><div class="stars">★★★★★</div></div>
  <div class="quote raised" style="left:445px"><h5>Ilsa Varney</h5><div class="role">Service: Geotechnical Conculting</div><p>Vivamus elementum semper nisi aenean eleifend tellus aenean leo ligula, porttitor.</p><div class="stars">★★★★★</div></div>
  <div class="quote" style="left:785px"><h5>Owen Carrick</h5><div class="role">Service: Geotechnical Conculting</div><p>Vivamus elementum semper nisi aenean eleifend tellus aenean leo ligula, porttitor.</p><div class="stars">★★★★★</div></div>
  <span class="avatar" style="left:90px" role="img" aria-label="Client portrait"></span>
  <span class="avatar" style="left:430px;background:#7f8a96" role="img" aria-label="Client portrait"></span>
  <span class="avatar" style="left:769px;background:#8a9098" role="img" aria-label="Client portrait"></span>
</section>

<footer class="footer">
  <div class="brand" style="top:40px;left:89px"><span class="brand-mark"></span><span class="brand-name" style="color:#fff">Brenlow Estates<small>LTD</small></span></div>
  <p class="footer-about">Lorem Ipsum is simply dummy text of the printing and typesetting industry. Lorem Ipsum has been the industry's standard dummy.</p>
  <h6 style="left:440px">We Provide</h6>
  <ul class="links"><li>Home</li><li>About us</li><li>Services</li><li>Property</li><li>Blog</li><li>Contact Us</li></ul>
  <h6 style="left:700px">Get In Touch</h6>
  <ul class="social">
    <li><span class="dot fill"></span><span class="blue">FEED</span></li>
    <li><span class="dot"></span><span>UPDATES</span></li>
    <li><span class="dot"></span><span>NETWORK</span></li>
  </ul>
  <h6 style="left:989px">Address</h6>
  <ul class="contact">
    <li><svg width="10" height="12" viewBox="0 0 10 12"><path d="M5 0a4 4 0 0 1 4 4c0 3-4 8-4 8S1 7 1 4a4 4 0 0 1 4-4z" fill="#fff"/></svg><span>12 Fountain Row<br>St Peter Port GY1 3LP</span></li>
    <li><svg width="10" height="10" viewBox="0 0 10 10"><path d="M1 1h3l1 2-1.5 1a6 6 0 0 0 2.5 2.5L7 5l2 1v3C4 9 1 6 1 1z" fill="#fff"/></svg><span>01481 700 120</span></li>
    <li><svg width="10" height="10" viewBox="0 0 10 10"><rect x="1" y="3" width="8" height="5" fill="#fff"/><rect x="3" y="1" width="4" height="2" fill="#fff"/></svg><span>Fax: 01481 700 121</span></li>
    <li><svg width="10" height="10" viewBox="0 0 10 10"><rect x="0" y="2" width="10" height="7" fill="#fff"/><path d="M0 2l5 4 5-4" stroke="#2b2b2b" fill="none"/></svg><span>hello@brenlow.example</span></li>
  </ul>
</footer>
<div class="base"><span class="copy">© 2016 - All Rights Reserved</span><span class="legal">Privacy Policy &nbsp;|&nbsp; Terms &amp; Condition</span></div>
<span class="to-top"><svg width="10" height="10" viewBox="0 0 10 10"><path d="M1 7l4-4 4 4" stroke="#fff" stroke-width="2" fill="none"/></svg></span>

</body>
</html>
```